Stylish Business Cards Wanted

- DOUBLE SIDED Design Required -

High end, edgy cards for a corporate and personal stylist. Must include logo,
Name: Belinda Harwick
Title: Director and Stylist
telephone : +61 8 7142 5809
email: belinda@theloombriefing.example
website: theloombriefing.example
Tag: Corporate Workwear & Uniform Specialist | Personal Stylist
Would like nice icons for telephone, email, website

Target Market(s)

Businesses wanting stylish uniforms, people wanting stylish wardrobes

Industry/Entity Type

Corporate Workwear Stylist

Contact Information for Business Card

I would like black, white and gold foiling incorporated in the design - possibly a touch of the other colours on my branding guide attached Name: Belinda Harwick Title: Director and Stylist telephone : +61 8 7142 5809 email: belinda@theloombriefing.example website: theloombriefing.example Tag: Corporate Workwear & Uniform Specialist | Personal Stylist Would like nice icons for telephone, email, website

Font styles to use
Other font styles liked:
• Raleway

Colors

Designer to choose colors to be used in the design.

Requirements
Must have
• Gold foil accents

```html
<!DOCTYPE html>
<html lang="en">
<head>
<meta charset="utf-8">
<title>The Loom Briefing – Business Cards</title>
<link rel="stylesheet" href="https://fonts.googleapis.com/css2?family=Dancing+Script:wght@600;700&family=Raleway:wght@600&family=Roboto:wght@400;500&display=swap">
<style>
  :root {
    --backdrop: #3b3b3d;
    --card-black: #1d1d1f;
    --gold: #e6bd5c;
    --white: #ffffff;
    --ink: #1a1a1a;
    --accent-pink: #e8127c;
  }
  html, body {
    margin: 0;
    padding: 0;
    width: 799px;
    height: 1200px;
    overflow: hidden;
    background: var(--backdrop);
  }
  .sheet {
    position: relative;
    width: 799px;
    height: 1200px;
  }
  .card {
    position: absolute;
    left: 90px;
    width: 620px;
    height: 355px;
    border-radius: 24px;
    background: var(--card-black);
    overflow: hidden;
    box-shadow: 0 10px 28px rgba(0,0,0,0.45);
  }
  .card--front { top: 120px; }
  .card--back { top: 700px; }

  .wordmark {
    font-family: 'Raleway', sans-serif;
    font-weight: 600;
    letter-spacing: 0.06em;
    text-transform: uppercase;
    margin: 0;
    white-space: nowrap;
  }
  .card--front .wordmark {
    position: absolute;
    left: 0; right: 0;
    top: 150px;
    text-align: center;
    font-size: 40px;
    color: var(--gold);
  }

  .accent-dot {
    position: absolute;
    left: -22px;
    top: 16px;
    width: 36px;
    height: 48px;
    border-radius: 50%;
    background: var(--accent-pink);
  }
  .holder {
    position: absolute;
    left: 46px;
    top: 26px;
  }
  .holder__name {
    margin: 0;
    font-family: 'Dancing Script', cursive;
    font-weight: 700;
    font-size: 32px;
    color: var(--gold);
    line-height: 1;
  }
  .holder__title {
    margin: 4px 0 0;
    font-family: 'Roboto', sans-serif;
    font-size: 14px;
    color: var(--white);
  }
  .contacts {
    position: absolute;
    left: 46px;
    top: 100px;
    margin: 0;
    padding: 0;
    list-style: none;
    font-family: 'Roboto', sans-serif;
    font-size: 15px;
    color: var(--white);
  }
  .contacts li {
    display: flex;
    align-items: center;
    gap: 10px;
    height: 25px;
  }
  .contacts svg { width: 14px; height: 14px; flex: none; }
  .social-square {
    width: 14px; height: 14px;
    background: var(--gold);
    border-radius: 3px;
    flex: none;
  }
  .card--back .wordmark {
    position: absolute;
    right: 40px;
    top: 110px;
    font-size: 30px;
    line-height: 1.1;
    text-align: right;
    color: var(--white);
  }
  .wave {
    position: absolute;
    left: 0; top: 0;
    width: 620px;
    height: 355px;
  }
  .tagline {
    position: absolute;
    right: 34px;
    bottom: 28px;
    margin: 0;
    padding: 0;
    list-style: none;
    text-align: right;
    font-family: 'Dancing Script', cursive;
    font-weight: 700;
    font-size: 18px;
    line-height: 22px;
    color: var(--ink);
  }
  .tagline li::after { content: "  «"; }
</style>
</head>
<body>
<main class="sheet">

  <section class="card card--front" aria-label="Card front">
    <p class="wordmark">The Loom Briefing</p>
  </section>

  <section class="card card--back" aria-label="Card back">
    <svg class="wave" viewBox="0 0 620 355" aria-hidden="true">
      <path d="M0,212 C160,225 280,275 620,178 L620,355 L0,355 Z" fill="var(--gold)"/>
      <path d="M0,232 C160,248 280,295 620,198 L620,210 C280,310 150,260 0,246 Z" fill="var(--card-black)"/>
      <path d="M0,260 C100,270 200,296 360,298 C200,306 100,286 0,274 Z" fill="var(--card-black)"/>
    </svg>

    <span class="accent-dot" aria-hidden="true"></span>

    <div class="holder">
      <h1 class="holder__name">Belinda Harwick</h1>
      <p class="holder__title">Director and Stylist</p>
    </div>

    <ul class="contacts">
      <li><span class="social-square" aria-hidden="true"></span>/theloombriefing101</li>
      <li>
        <svg viewBox="0 0 24 24" aria-hidden="true"><circle cx="12" cy="12" r="10.5" fill="none" stroke="var(--gold)" stroke-width="2"/><path d="M8.5 7.5l2 2-1 1.5c.8 1.6 1.9 2.7 3.5 3.5l1.5-1 2 2-1.2 1.5c-3.8-.6-7.2-4-7.8-7.8z" fill="var(--gold)"/></svg>
        +61 8 7142 5809
      </li>
      <li>
        <svg viewBox="0 0 24 24" aria-hidden="true"><rect x="2.5" y="5" width="19" height="14" rx="1.5" fill="none" stroke="var(--gold)" stroke-width="2"/><path d="M3 6l9 7 9-7" fill="none" stroke="var(--gold)" stroke-width="2"/></svg>
        belinda@theloombriefing.example
      </li>
      <li>
        <svg viewBox="0 0 24 24" aria-hidden="true"><circle cx="12" cy="12" r="10" fill="none" stroke="var(--gold)" stroke-width="2"/><ellipse cx="12" cy="12" rx="4.5" ry="10" fill="none" stroke="var(--gold)" stroke-width="1.6"/><path d="M2 12h20M4 7h16M4 17h16" stroke="var(--gold)" stroke-width="1.4"/></svg>
        theloombriefing.example
      </li>
    </ul>

    <p class="wordmark">The Loom<br>Briefing</p>

    <ul class="tagline">
      <li>Personal Stylist</li>
      <li>Corporate Workwear</li>
      <li>and Uniform Specialist</li>
    </ul>
  </section>

</main>
</body>
</html>
```